Web Site Mock Up's for a Dog Food Business

We are a supplier of bespoke dog food. We tailor our dog food to meet the dogs needs.We are looking for ideas (mock ups) of design ideas for our new web site - Just mock ups - web site will follow if we are happy with the mock ups.I have included our logo (PSD file). I have also included a rough (please don’t copy) home page with the information we would ideally like on the page. Note the page will have sliders at the top, we have done two example sliders, and included a video to be included.I have also enclosed the questions we need to find out in order to develop a dogs food.I would like to see a home page, and a tell us about your dog page.Would like mock ups as PSD files, so we can play around with.I am open to ideas and better designs. DO NOT JUST COPY MY LAYOUTSome of our competitors sites include www.tails.comwww.paws.comwww.parcelpet.comwww.growlingtums.co.ukI want a clean, bright easy to navigate site. Happy to play around with colours - doesn’t have to be the browns I have used. Happy to use both infographics and photo of real dogs, but I do want site to look like the best food available for dogs.Web site will be a database driven site, with around 10 -15 pages plus about 60 dynamic database driven pages of products (all same layout )Look forward to receiving your ideas.

```html
<!DOCTYPE html>
<html lang="en">
<head>
<meta charset="utf-8">
<title>Kibble Crate – Bespoke Dog Food</title>
<link rel="stylesheet" href="https://fonts.googleapis.com/css2?family=Fjalla+One&family=Poppins:wght@400;500;600&display=swap">
<style>
:root{
  --brown:#4a2a17;
  --brown-deep:#3a2012;
  --brown-soft:#6b4128;
  --cream:#f4f2f0;
  --sand:#f1ece8;
  --peach:#fde9dc;
  --grey-box:#f3f3f3;
  --ink:#2b2b2b;
  --muted:#555;
  --night:#1d1914;
  --white:#fff;
}
*{margin:0;padding:0;box-sizing:border-box}
html,body{width:1200px;height:3863px;overflow:hidden}
body{position:relative;background:var(--white);font-family:'Poppins',sans-serif;color:var(--ink)}
.abs{position:absolute}
.display{font-family:'Fjalla One',sans-serif;color:var(--brown);font-weight:400}

/* header */
.site-header{left:0;top:0;width:1200px;height:103px;background:var(--brown)}
.brand{left:116px;top:30px;height:46px;padding:0 18px;background:var(--white);border-radius:0 0 40px 40px;display:flex;align-items:center;gap:8px;font-weight:600;font-size:17px;color:var(--brown)}
.brand-dot{width:12px;height:12px;border-radius:50%;background:var(--brown)}
.login{right:118px;top:20px;color:var(--white);font-size:13px;text-decoration:underline}
.nav{left:430px;top:62px;display:flex;gap:31px;color:var(--white);font-size:13.5px}

/* hero */
.hero{left:0;top:103px;width:1200px;height:507px;background:var(--cream)}
.hero-photo{left:155px;top:103px;width:373px;height:412px;background:radial-gradient(ellipse at 55% 55%,#c8a47a 0%,#8b5a34 35%,#e9e6e2 72%,var(--cream) 100%)}
.play{left:300px;top:282px}
.hero-title{left:566px;top:206px;font-size:35px;line-height:50px;white-space:nowrap}
.btn{display:flex;align-items:center;justify-content:center;background:var(--brown);color:var(--white);font-weight:600;border-radius:40px}
.hero-btn{left:566px;top:342px;width:289px;height:47px;font-size:15px}
.dots{display:flex;gap:9px}
.dot{width:11px;height:11px;border-radius:50%;border:2px solid var(--brown)}
.dot.on{background:var(--brown)}
.hero-dots{left:569px;top:469px}

/* how it works */
.section-title{width:1200px;left:0;text-align:center;font-size:38px}
.step-art{width:237px;height:237px;border-radius:50%;background:radial-gradient(circle at 50% 55%,#d9c3a8 0%,#efe8e1 45%,#f1f1f1 70%)}
.step-label{width:300px;text-align:center;font-size:23px}
.step-text{width:300px;text-align:center;font-size:13.5px;line-height:32px;color:var(--muted)}

/* foods */
.foods{left:0;top:1270px;width:1200px;height:854px;background:var(--sand)}
.foods-intro{left:0;width:1200px;text-align:center;font-size:13.5px;color:var(--ink)}
.foods-btn{left:518px;top:1501px;width:164px;height:47px;font-size:14px}
.card{width:232px;height:432px;top:1602px;background:var(--white);box-shadow:0 1px 4px rgba(0,0,0,.12)}
.card-photo{width:232px;height:175px;border:2px solid var(--brown)}
.card h3{font-family:'Fjalla One',sans-serif;font-weight:400;font-size:19px;color:var(--ink);margin:14px 0 0 18px}
.card p{font-size:12.5px;line-height:26px;margin:6px 16px 0 18px;color:var(--ink)}
.card-btn{left:18px;top:373px;width:160px;height:36px;border:1.5px solid var(--brown);border-radius:30px;display:flex;align-items:center;justify-content:center;font-size:12.5px;color:var(--brown)}

/* testimonial */
.testimonial{left:0;top:2124px;width:1200px;height:443px;background:linear-gradient(100deg,#4a2b1a 0%,#6b4128 55%,#3d2314 100%)}
.customer-photo{left:114px;top:2212px;width:263px;height:263px;border-radius:50%;background:radial-gradient(circle at 50% 45%,#d8b890,#a67446 60%,#7a5235)}
.quote-title{left:440px;top:2230px;font-size:38px;color:var(--white)}
.quote-text{left:440px;font-size:13.5px;color:#f1e6dc}
.quote-name{left:440px;top:2389px;font-size:13.5px;color:#f1e6dc}
.quote-name b{font-weight:600}
.t-dot{width:9px;height:9px;border-radius:50%;background:#a88a74}
.t-dot.on{background:var(--white)}

/* faq */
.faq-box{width:462px;height:76px;padding:12px 24px 0 52px;font-size:13.5px;line-height:25px}
.faq-box .tag{position:absolute;left:30px;top:12px;font-weight:600}
.faq-q{left:118px;background:var(--grey-box);color:var(--ink)}
.faq-a{left:618px;background:var(--peach);color:var(--ink)}
.faq-btn{left:533px;top:3098px;width:134px;height:39px;font-size:14px}

/* contact */
.night{left:0;top:3380px;width:1200px;height:483px}
.contact-card{left:306px;top:3270px;width:588px;height:368px;background:var(--brown);border:6px solid #e8dfd6}
.contact-brand{left:500px;top:3228px;width:200px;height:64px;background:var(--white);border-radius:0 0 60px 60px;display:flex;align-items:center;justify-content:center;gap:8px;font-weight:600;font-size:16px;color:var(--brown)}
.contact-title{left:306px;top:3318px;width:588px;text-align:center;font-size:38px;color:var(--white)}
.field{background:var(--white);font-size:12.5px;color:#888;padding:13px 14px}
.submit{left:530px;top:3623px;width:140px;height:39px;border:1.5px solid #e8dfd6;border-radius:30px;background:var(--brown);color:var(--white);font-size:14px;font-weight:500;display:flex;align-items:center;justify-content:center}
.follow{left:0;top:3753px;width:1200px;text-align:center;color:var(--white);font-weight:600;font-size:14px}
.social{left:570px;top:3794px;display:flex;gap:16px}
.social span{width:18px;height:18px;background:var(--white);border-radius:3px}
.copyright{left:0;top:3832px;width:1200px;text-align:center;color:#ddd;font-size:11.5px}
</style>
</head>
<body>

<header class="abs site-header"></header>
<div class="abs brand"><span class="brand-dot"></span>kibblecrate.co.uk</div>
<div class="abs login">Log in</div>
<nav class="abs nav"><span>Home</span><span>Our Food</span><span>How It Works</span><span>Pricing</span><span>Customer Reviews</span><span>FAQ</span><span>Contact Us</span></nav>

<section class="abs hero"></section>
<div class="abs hero-photo" role="img" aria-label="Beagle puppy eating from a steel food bowl"></div>
<svg class="abs play" width="46" height="52" viewBox="0 0 46 52"><polygon points="4,3 42,26 4,49" fill="none" stroke="#fff" stroke-width="4" stroke-linejoin="round"/></svg>
<h1 class="abs display hero-title">food unique as your dog blended<br>using the finest ingredients</h1>
<div class="abs btn hero-btn">TELL US ABOUT YOUR DOG</div>
<div class="abs dots hero-dots"><span class="dot on"></span><span class="dot"></span><span class="dot"></span><span class="dot"></span></div>

<h2 class="abs display section-title" style="top:690px">How It Works</h2>
<div class="abs step-art" style="left:114px;top:796px" role="img" aria-label="Illustrated puppy sitting"></div>
<div class="abs step-art" style="left:482px;top:796px" role="img" aria-label="Illustrated puppy beside a food bowl"></div>
<div class="abs step-art" style="left:852px;top:796px" role="img" aria-label="Illustrated puppy pushing a delivery box"></div>
<div class="abs display step-label" style="left:82px;top:1047px">01.Tell us about your dog</div>
<div class="abs display step-label" style="left:450px;top:1047px">02.We Create Your Food</div>
<div class="abs display step-label" style="left:820px;top:1047px">03.We Delivery</div>
<p class="abs step-text" style="left:82px;top:1092px">Lorem ipsum dolor sit amet,<br>consectetur adipiscing elit, sed do<br>eiusmpor incididun</p>
<p class="abs step-text" style="left:450px;top:1092px">Lorem ipsum dolor sit amet,<br>consectetur adipiscing elit, sed do<br>eiusmpor incididun</p>
<p class="abs step-text" style="left:820px;top:1092px">Lorem ipsum dolor sit amet,<br>consectetur adipiscing elit, sed do<br>eiusmpor incididun</p>

<section class="abs foods"></section>
<h2 class="abs display section-title" style="top:1352px">Our Foods</h2>
<p class="abs foods-intro" style="top:1421px">We develop and create your dogs ideal food using the finest ingredients, based on your dogs requirements.</p>
<p class="abs foods-intro" style="top:1452px">Our foods are developed by pet nutritionalists, approved by vets and enjoyed by all dogs.</p>
<div class="abs btn foods-btn">START NOW</div>

<svg class="abs" style="left:46px;top:1802px" width="20" height="32" viewBox="0 0 20 32"><polyline points="16,3 4,16 16,29" fill="none" stroke="#222" stroke-width="3.5"/></svg>
<svg class="abs" style="left:1134px;top:1802px" width="20" height="32" viewBox="0 0 20 32"><polyline points="4,3 16,16 4,29" fill="none" stroke="#222" stroke-width="3.5"/></svg>

<article class="abs card" style="left:111px">
  <div class="card-photo" role="img" aria-label="Senior dog eating from a bowl" style="background:linear-gradient(160deg,#d7b286,#9c6a3c 60%,#c9c5bf)"></div>
  <h3>SENIOR FOOD</h3>
  <p>The right balance of protein and energy to help reduce joint pain, while maintaining weight to keep your dog active</p>
  <div class="abs card-btn">TELL ME MORE</div>
</article>
<article class="abs card" style="left:358px">
  <div class="card-photo" role="img" aria-label="Adult dog beside a bowl of kibble" style="background:linear-gradient(160deg,#a7845e,#5c3a20 60%,#8a6a4a)"></div>
  <h3>ADULT FOOD</h3>
  <p>Careful balance of proteins, fats and oils, minerals, vitamins and carbohydrates are needed as an adult and differ between breeds</p>
  <div class="abs card-btn">TELL ME MORE</div>
</article>
<article class="abs card" style="left:608px">
  <div class="card-photo" role="img" aria-label="Golden puppy with a pile of kibble" style="background:linear-gradient(180deg,#f6f1ea,#e0b879 55%,#7a4e2c)"></div>
  <h3>PUPPY FOOD</h3>
  <p>A well balanced and nutritious range of foods to meet the needs of growing puppies of all breeds</p>
  <div class="abs card-btn">TELL ME MORE</div>
</article>
<article class="abs card" style="left:855px">
  <div class="card-photo" role="img" aria-label="Spaniel eating from a food bowl" style="background:linear-gradient(160deg,#efe9e2,#b27a4a 55%,#e4ded6)"></div>
  <h3>SPECIALIST FOODS</h3>
  <p>We provide grain free and hypoallergenic foods for fussy eaters, dogs with allergies and food intolerances.</p>
  <div class="abs card-btn">TELL ME MORE</div>
</article>

<section class="abs testimonial" role="img" aria-label="Close-up of dog kibble in a bowl"></section>
<div class="abs customer-photo" role="img" aria-label="Customer hugging her dog"></div>
<h2 class="abs display quote-title">What Our Customers Say</h2>
<p class="abs quote-text" style="top:2319px">I have 3 dogs all on different foods.</p>
<p class="abs quote-text" style="top:2350px">No more trips to the shops fetching massive bags of food. This works for me and my dogs love it.</p>
<p class="abs quote-name"><b>MAYA WITH BRUNO</b> – Halbrook</p>
<div class="abs dots" style="left:443px;top:2465px;gap:10px"><span class="t-dot on"></span><span class="t-dot"></span><span class="t-dot"></span></div>

<h2 class="abs display section-title" style="top:2650px">Faq</h2>
<div class="abs faq-box faq-q" style="top:2737px"><span class="tag">Q)</span>At vero eos et accusamus et iusto odio dignissimos mus qui blanditiis praesentium ?</div>
<div class="abs faq-box faq-a" style="top:2737px"><span class="tag">A)</span>At vero eos et accusamus et iusto odio dignissimos mus qui blanditiis praesentium</div>
<div class="abs faq-box faq-q" style="top:2854px"><span class="tag">Q)</span>At vero eos et accusamus et iusto odio dignissimos mus qui blanditiis praesentium ?</div>
<div class="abs faq-box faq-a" style="top:2854px"><span class="tag">A)</span>At vero eos et accusamus et iusto odio dignissimos mus qui blanditiis praesentium</div>
<div class="abs faq-box faq-q" style="top:2974px"><span class="tag">Q)</span>At vero eos et accusamus et iusto odio dignissimos mus qui blanditiis praesentium ?</div>
<div class="abs faq-box faq-a" style="top:2974px"><span class="tag">A)</span>At vero eos et accusamus et iusto odio dignissimos mus qui blanditiis praesentium</div>
<div class="abs btn faq-btn">View All</div>

<svg class="abs night" viewBox="0 0 1200 483" preserveAspectRatio="none"><path d="M0 110 Q600 -60 1200 110 L1200 483 L0 483 Z" fill="#1d1914"/></svg>
<div class="abs contact-card"></div>
<div class="abs contact-brand"><span class="brand-dot"></span>kibblecrate.co.uk</div>
<h2 class="abs display contact-title">Contact Us</h2>
<div class="abs field" style="left:350px;top:3391px;width:242px;height:47px">Name</div>
<div class="abs field" style="left:608px;top:3391px;width:242px;height:47px">Email</div>
<div class="abs field" style="left:350px;top:3456px;width:242px;height:46px">Phone No</div>
<div class="abs field" style="left:608px;top:3456px;width:242px;height:46px">Address</div>
<div class="abs field" style="left:350px;top:3517px;width:500px;height:67px;padding-top:10px">Message</div>
<div class="abs submit">SUBMIT</div>

<div class="abs follow">FOLLOW US</div>
<div class="abs social"><span aria-label="Social link"></span><span aria-label="Social link"></span></div>
<p class="abs copyright">© 2018 Copyrights Kibble Crate All Rights Reserved</p>

</body>
</html>
```